Website Design - TallyPorchHelpers.net

PLEASE CHECK WORD DOCUMENT ATTACHED FOR WEBSITE FLOW.

Target Market(s)

REAL ESTATE AGENTS ARE THE TARGET MARKET

Industry/Entity Type

Real Estate

Coding

Coded - Design and coding required

Number of Pages Required

4 page

Colors

Designer to choose colors to be used in the design.

Requirements
Must have
• WE LIKE RED LOGO ATTACHED
Nice to have
• PLEASE CHECK WORD DOCUMENT ATTACHED FOR WEBSITE FLOW.
Should not have

```html
<!DOCTYPE html>
<html lang="en">
<head>
<meta charset="utf-8">
<title>TallyPorchHelpers.net</title>
<link href="https://fonts.googleapis.com/css2?family=Roboto+Condensed:wght@400;700&family=Roboto:wght@400;500;700&display=swap" rel="stylesheet">
<style>
:root{
  --red:#d2161e;
  --red-dark:#a80f15;
  --blue:#1f45a8;
  --blue-light:#2c5cb5;
  --navy:#201d7e;
  --ice:#dfeaf7;
  --ink:#222;
  --muted:#555;
  --black:#0d0d0d;
  --white:#fff;
}
*{box-sizing:border-box;margin:0;padding:0}
html,body{width:1200px;height:4749px;overflow:hidden}
body{position:relative;font-family:'Roboto',sans-serif;color:var(--ink);background:var(--white)}
.abs{position:absolute}
.heading{font-family:'Roboto Condensed',sans-serif;font-weight:400;text-transform:uppercase;font-size:36px;text-align:center;width:1200px;left:0;color:#111}

/* header */
.site-header{top:0;left:0;width:1200px;height:125px;background:var(--white)}
.brand{left:92px;top:40px;display:flex;align-items:center;gap:12px;font-family:'Roboto',sans-serif;font-weight:700;font-size:24px;color:var(--red)}
.brand-mark{width:26px;height:26px;background:var(--red)}
.phone-top{right:92px;top:28px;font-size:15px;display:flex;align-items:center;gap:8px;color:#222}
.main-nav{right:92px;top:72px;display:flex;gap:44px;font-size:16px;color:#222}

/* hero */
.hero{top:125px;left:0;width:1200px;height:510px;background:linear-gradient(180deg,#9fc2dc 0%,#7d95a5 30%,#56703f 62%,#3d5a2a 85%,#6c6c60 100%)}
.hero-text{top:318px;right:92px;width:560px;text-align:right;color:var(--white);font-size:27px;line-height:37px;text-shadow:0 1px 3px rgba(0,0,0,.5)}

/* options */
.options{top:635px;left:0;width:1200px;height:245px;background:linear-gradient(180deg,#1c3f9e,#2552b4)}
.options .heading{top:58px;color:var(--white);font-size:31px}
.opt-btn{top:131px;height:52px;background:var(--white);border-radius:3px;font-family:'Roboto Condensed',sans-serif;font-weight:700;font-size:16px;color:#111;display:flex;align-items:center;justify-content:center;box-shadow:0 2px 4px rgba(0,0,0,.25)}

/* how it works */
.how .heading{top:980px}
.step{top:1086px;width:323px;height:259px;text-align:center}
.step.featured{background:var(--white);box-shadow:0 1px 6px rgba(0,0,0,.25)}
.step-icon{position:absolute;left:111px;top:29px;width:100px;height:100px;border-radius:50%;background:var(--blue-light);display:flex;align-items:center;justify-content:center}
.step p{position:absolute;top:152px;left:25px;width:273px;font-size:15.5px;line-height:21px;color:#333}

/* services */
.services-band{top:1440px;left:0;width:1200px;height:385px;background:linear-gradient(180deg,#c4141b,#9e0e13 60%,#c4141b)}
.services .heading{top:1510px;color:var(--white)}
.service-card{top:1608px;width:325px;height:418px;background:var(--white);box-shadow:0 1px 6px rgba(0,0,0,.2);text-align:center}
.service-photo{height:212px;width:100%}
.service-card h3{font-weight:400;font-size:19px;margin-top:32px;color:#222}
.service-card p{font-size:13.5px;line-height:19px;color:#555;width:270px;margin:12px auto 0}
.pill{display:inline-block;margin-top:14px;background:var(--red);color:var(--white);font-size:13px;padding:6px 22px;border-radius:15px}

/* pricing */
.pricing .heading{top:2158px}
.price-card{top:2248px;width:190px;height:373px;background:var(--white);border:1px solid #bbb;box-shadow:0 1px 4px rgba(0,0,0,.15);text-align:center}
.price-card h4{font-family:'Roboto Condensed',sans-serif;font-weight:700;font-size:17px;height:38px;line-height:38px}
.price-band{height:57px;background:var(--navy);color:var(--white);font-family:'Roboto Condensed',sans-serif;font-weight:700;font-size:14px;line-height:19px;padding-top:10px}
.price-badge{position:absolute;left:55px;top:55px;width:80px;height:80px;border-radius:50%;background:var(--red);border:4px solid var(--white);color:var(--white);font-family:'Roboto Condensed',sans-serif;font-weight:700;font-size:25px;line-height:72px;box-shadow:0 0 0 1px #ddd}
.price-list{position:absolute;top:146px;left:14px;width:162px;font-size:11.5px;line-height:15px;color:#444}
.price-list li{list-style:none;margin-bottom:11px}
.price-card.custom .price-list{top:102px}
.buy{position:absolute;bottom:22px;left:0;width:100%;color:var(--red);font-size:12.5px;font-weight:500}

/* subscription */
.subscribe{top:2729px;left:0;width:1200px;height:706px;background:var(--ice)}
.subscribe .heading{top:82px;font-size:34px;line-height:48px}
.perk{top:250px;width:240px;text-align:center}
.perk-icon{width:110px;height:110px;border-radius:50%;border:2px solid #4a7bc4;background:var(--white);margin:0 auto;display:flex;align-items:center;justify-content:center}
.perk h5{font-weight:700;font-size:18px;margin-top:38px;color:#111}
.perk p{font-size:14.5px;line-height:21px;margin-top:14px;color:#444}
.signup-btn{top:596px;left:538px;width:120px;height:48px;background:var(--red);color:var(--white);font-size:17px;font-weight:500;display:flex;align-items:center;justify-content:center;box-shadow:0 2px 4px rgba(0,0,0,.25)}

/* faq */
.faq .heading{top:3532px}
.faq-item{left:174px;width:855px;height:90px;background:var(--white);border-left:6px solid var(--red);box-shadow:0 1px 5px rgba(0,0,0,.22);padding:18px 30px}
.faq-item .q{color:var(--red);font-size:18px}
.faq-item .a{color:#444;font-size:14px;margin-top:8px}

/* testimonial */
.testimonial{top:4147px;left:0;width:1200px;height:184px;background:var(--navy);text-align:center;color:var(--white)}
.quote-mark{position:absolute;left:565px;top:-35px;width:70px;height:70px;border-radius:50%;background:var(--white);display:flex;align-items:center;justify-content:center}
.testimonial p{position:absolute;top:58px;left:150px;width:900px;font-size:15px;line-height:31px}
.testimonial cite{position:absolute;top:136px;left:0;width:1200px;font-size:14px;font-style:italic}

/* footer */
.site-footer{top:4331px;left:0;width:1200px;height:418px;background:var(--black);color:var(--white)}
.foot-col{top:95px}
.foot-col h6{font-weight:400;font-size:21px;text-transform:uppercase;margin-bottom:18px}
.foot-col p{font-size:15px;line-height:30px;color:#ddd}
.foot-col ul{list-style:none;font-size:15px;line-height:33px;color:#ddd}
.contact-line{display:flex;gap:14px;margin-bottom:18px}
.contact-line b{display:block;font-size:14px;font-weight:700;letter-spacing:.5px}
.contact-line span{font-size:14px;line-height:19px;color:#ddd}
.copyright{top:355px;left:0;width:1200px;height:63px;border-top:1px solid #222;text-align:center;line-height:63px;font-size:13px;color:#aaa}
</style>
</head>
<body>

<header class="site-header abs">
  <div class="brand abs"><span class="brand-mark"></span>TallyPorchHelpers.net</div>
  <div class="phone-top abs">
    <svg width="22" height="22" viewBox="0 0 24 24"><circle cx="12" cy="12" r="11" fill="none" stroke="#d2161e" stroke-width="2"/><path d="M8 6l2 0 1 3-1.5 1a7 7 0 0 0 4 4l1-1.5 3 1v2c0 1-1 1.5-2 1.5A10 10 0 0 1 6.5 8C6.5 7 7 6 8 6z" fill="#d2161e"/></svg>
    Call Or Text Us: 1-555-014-2287
  </div>
  <nav class="main-nav abs"><span>How it works</span><span>Service</span><span>Pricing</span><span>About us</span><span>Faq</span><span>Contact</span></nav>
</header>

<section class="hero abs" role="img" aria-label="Photo of a suburban house with an open house sign post on the front lawn">
</section>
<p class="hero-text abs">Helping agents save time and money. We place signs and boost foot traffic to your open houses using proven marketing techniques.</p>

<section class="options abs">
  <h2 class="heading abs">Choose the option below that best describes you</h2>
  <div class="opt-btn abs" style="left:184px;width:259px">I'M A FULL ON BROKERAGE</div>
  <div class="opt-btn abs" style="left:465px;width:273px">I'M AN IND. BROKER WITH A TEAM</div>
  <div class="opt-btn abs" style="left:753px;width:260px">I NEED SIGN PLACEMENT ASAP</div>
</section>

<section class="how">
  <h2 class="heading abs">How it works</h2>
  <div class="step abs" style="left:89px">
    <div class="step-icon"><svg width="44" height="52" viewBox="0 0 44 52"><path d="M22 3a15 15 0 0 0-15 15c0 11 15 26 15 26s15-15 15-26A15 15 0 0 0 22 3z" fill="none" stroke="#fff" stroke-width="3"/><circle cx="22" cy="18" r="5" fill="#fff"/><ellipse cx="22" cy="48" rx="12" ry="3" fill="none" stroke="#fff" stroke-width="2"/></svg></div>
    <p>Place signs strategically in best areas according to where the open house is located</p>
  </div>
  <div class="step featured abs" style="left:437px">
    <div class="step-icon"><svg width="54" height="50" viewBox="0 0 54 50"><path d="M5 22L27 4l22 18" fill="none" stroke="#fff" stroke-width="3"/><rect x="11" y="20" width="32" height="26" fill="none" stroke="#fff" stroke-width="3"/><rect x="17" y="27" width="20" height="9" fill="#fff"/><rect x="24" y="36" width="6" height="10" fill="#fff"/></svg></div>
    <p>Pick Up the signs after the open house</p>
  </div>
  <div class="step abs" style="left:782px">
    <div class="step-icon"><svg width="52" height="50" viewBox="0 0 52 50"><rect x="5" y="8" width="42" height="24" fill="none" stroke="#fff" stroke-width="3"/><line x1="11" y1="16" x2="41" y2="16" stroke="#fff" stroke-width="3"/><line x1="11" y1="23" x2="34" y2="23" stroke="#fff" stroke-width="3"/><line x1="15" y1="32" x2="15" y2="46" stroke="#fff" stroke-width="3"/><line x1="37" y1="32" x2="37" y2="46" stroke="#fff" stroke-width="3"/></svg></div>
    <p>Store custom signs for you if needed</p>
  </div>
</section>

<section class="services">
  <div class="services-band abs"></div>
  <h2 class="heading abs">Our services</h2>
  <div class="service-card abs" style="left:89px">
    <div class="service-photo" role="img" aria-label="Photo of a house with a for sale sign" style="background:linear-gradient(180deg,#b9c7d3,#8d8878 55%,#5c6e3e)"></div>
    <h3>Neque porro quisquam</h3>
    <p>It is a long established fact that a reader will be distracted by the readable content of a page when looking at its layout.</p>
    <span class="pill">View More</span>
  </div>
  <div class="service-card abs" style="left:434px">
    <div class="service-photo" role="img" aria-label="Photo of a for rent sign in front of a house" style="background:linear-gradient(180deg,#c9d2da,#a9a699 55%,#6f7d56)"></div>
    <h3>Dolorem ipsum quia</h3>
    <p>It is a long established fact that a reader will be distracted by the readable content of a page when looking at its layout.</p>
    <span class="pill">View More</span>
  </div>
  <div class="service-card abs" style="left:782px">
    <div class="service-photo" role="img" aria-label="Photo of a white house with a garage" style="background:linear-gradient(180deg,#c5d4e2,#d8d6cf 45%,#7b8a5a)"></div>
    <h3>Neque porro quisquam</h3>
    <p>It is a long established fact that a reader will be distracted by the readable content of a page when looking at its layout.</p>
    <span class="pill">View More</span>
  </div>
</section>

<section class="pricing">
  <h2 class="heading abs">Pricing package</h2>
  <div class="price-card abs" style="left:79px">
    <h4>5 Signs</h4><div class="price-band"></div><div class="price-badge">$49</div>
    <ul class="price-list"><li>1. Place signs strategically in best areas according to where the open house is located</li><li>2. Pick Up the signs after the open house</li><li>3. Store custom signs for you if needed</li></ul>
    <div class="buy">BUY NOW »</div>
  </div>
  <div class="price-card abs" style="left:288px">
    <h4>10 Signs</h4><div class="price-band"></div><div class="price-badge">$59</div>
    <ul class="price-list"><li>1. Place signs strategically in best areas according to where the open house is located</li><li>2. Pick Up the signs after the open house</li><li>3. Store custom signs for you if needed</li></ul>
    <div class="buy">BUY NOW »</div>
  </div>
  <div class="price-card abs" style="left:500px">
    <h4>15 Signs</h4><div class="price-band"></div><div class="price-badge">$69</div>
    <ul class="price-list"><li>1. Place signs strategically in best areas according to where the open house is located</li><li>2. Pick Up the signs after the open house</li><li>3. Store custom signs for you if needed</li></ul>
    <div class="buy">BUY NOW »</div>
  </div>
  <div class="price-card abs" style="left:709px">
    <h4>20 Signs</h4><div class="price-band"></div><div class="price-badge">$79</div>
    <ul class="price-list"><li>1. Place signs strategically in best areas according to where the open house is located</li><li>2. Pick Up the signs after the open house</li><li>3. Store custom signs for you if needed</li></ul>
    <div class="buy">BUY NOW »</div>
  </div>
  <div class="price-card custom abs" style="left:918px;width:196px">
    <h4>25+ Signs</h4><div class="price-band">Click Buy Now<br>To Create Custom Pkg</div>
    <ul class="price-list"><li>1. Place signs strategically in best areas according to where the open house is located</li><li>2. Pick Up the signs after the open house</li><li>3. Store custom signs for you if needed</li></ul>
    <div class="buy">BUY NOW »</div>
  </div>
</section>

<section class="subscribe abs">
  <h2 class="heading abs">Sign up for a subscription and get these<br>marketing services for free</h2>
  <div class="perk abs" style="left:66px">
    <div class="perk-icon"><svg width="48" height="44" viewBox="0 0 48 44"><path d="M4 4h40v26H20l-9 9v-9H4z" fill="none" stroke="#2c5cb5" stroke-width="2.5"/><circle cx="16" cy="17" r="2" fill="#2c5cb5"/><circle cx="24" cy="17" r="2" fill="#2c5cb5"/><circle cx="32" cy="17" r="2" fill="#2c5cb5"/></svg></div>
    <h5>SMS</h5><p>Send sms blast to your neighborhood informing them your home is for sale and if they know anyone looking to send them over</p>
  </div>
  <div class="perk abs" style="left:341px">
    <div class="perk-icon"><svg width="50" height="36" viewBox="0 0 50 36"><rect x="3" y="3" width="44" height="30" fill="none" stroke="#2c5cb5" stroke-width="2.5"/><path d="M3 3l22 18L47 3M3 33l16-15M47 33L31 18" fill="none" stroke="#2c5cb5" stroke-width="2.5"/></svg></div>
    <h5>EMAIL</h5><p>Email blast to your neighborhood informing them your home is for sale and if they know anyone looking to send them over</p>
  </div>
  <div class="perk abs" style="left:616px">
    <div class="perk-icon"><svg width="40" height="40" viewBox="0 0 40 40"><rect x="3" y="3" width="34" height="34" rx="3" fill="none" stroke="#2c5cb5" stroke-width="2.5"/></svg></div>
    <h5>FB AD</h5><p>Newsfeed ads to people in your open house area</p>
  </div>
  <div class="perk abs" style="left:891px">
    <div class="perk-icon"><svg width="46" height="46" viewBox="0 0 46 46"><path d="M24 4h18v18L20 44 2 26z" fill="none" stroke="#2c5cb5" stroke-width="2.5"/><circle cx="34" cy="12" r="3" fill="none" stroke="#2c5cb5" stroke-width="2.5"/></svg></div>
    <h5>VB</h5><p>VB blast to your neighborhood informing them your home is for sale and if they know anyone looking to send them over</p>
  </div>
  <div class="signup-btn abs">SIGN UP</div>
</section>

<section class="faq">
  <h2 class="heading abs">FAQ</h2>
  <div class="faq-item abs" style="top:3625px"><div class="q">Q- Why choose Porch Crew ?</div><div class="a">A- It is a long established fact that a reader will be distracted by the readable content of a page .</div></div>
  <div class="faq-item abs" style="top:3729px"><div class="q">Q- quisquam est qui dolorem ipsum quia dolor sit amet?</div><div class="a">A- The point of using Lorem Ipsum is that it has a more-or-less normal distribution of letters, as opposed</div></div>
  <div class="faq-item abs" style="top:3833px"><div class="q">Q- Neque porro quisquam est qui dolorem ipsum quia dolor sit amet?</div><div class="a">A- Lorem Ipsum as their default model text, and a search for 'lorem ipsum' will uncover many web sites.</div></div>
  <div class="faq-item abs" style="top:3937px"><div class="q">Q- Porro quisquam est qui dolorem ipsum quia dolor sit amet, consectetur?</div><div class="a">A- Various versions have evolved over the years, sometimes by accident, sometimes on purpose</div></div>
</section>

<section class="testimonial abs">
  <div class="quote-mark"><svg width="32" height="24" viewBox="0 0 32 24"><path d="M2 24V13C2 6 6 2 12 1v4c-3 1-5 3-5 7h5v12zM18 24V13c0-7 4-11 10-12v4c-3 1-5 3-5 7h5v12z" fill="#201d7e"/></svg></div>
  <p>The point of using Lorem Ipsum is that it has a more-or-less normal distribution of letters, as opposed to using 'Content here, content here', making it look like readable English Many desktop publishing packages and web page editors now</p>
  <cite>- Neque porro quisquam</cite>
</section>

<footer class="site-footer abs">
  <div class="foot-col abs" style="left:89px;width:340px">
    <h6>About us</h6>
    <p>Helping agents leverage their time and skills to increase production at an affordable price with impeccable support.</p>
  </div>
  <div class="foot-col abs" style="left:516px;width:240px">
    <h6>Contact us</h6>
    <div class="contact-line"><svg width="22" height="26" viewBox="0 0 22 26"><path d="M11 2a8 8 0 0 0-8 8c0 6 8 14 8 14s8-8 8-14a8 8 0 0 0-8-8z" fill="none" stroke="#fff" stroke-width="2"/><circle cx="11" cy="10" r="3" fill="#fff"/></svg><div><b>ADDRESS</b><span>48 Linden Row, Suite 2<br>Cary, NC 27519</span></div></div>
    <div class="contact-line"><svg width="22" height="22" viewBox="0 0 24 24"><path d="M7 3l3 0 1.5 4.5-2 1.5a10 10 0 0 0 5.5 5.5l1.5-2L21 14v3c0 2-1.5 3-3 3A15 15 0 0 1 4 6c0-1.5 1-3 3-3z" fill="none" stroke="#fff" stroke-width="2"/></svg><div><b>PHONE NUMBER</b><span>(555) 018-4432</span></div></div>
  </div>
  <div class="foot-col abs" style="left:814px">
    <h6>About</h6>
    <ul><li>Home</li><li>About Us</li><li>Services</li><li>Training</li></ul>
  </div>
  <div class="foot-col abs" style="left:991px">
    <h6>Resources</h6>
    <ul><li>Support</li><li>Why Us</li><li>Testimonials</li><li>FAQ</li></ul>
  </div>
  <div class="copyright abs">© 2018 Company Name&nbsp; All right reserved</div>
</footer>

</body>
</html>
```